Holiday Rental Company Flyer Design (DL not A5)

Note from Brandloom Administration: The category sizing selected is A5, however the project requires DL sized artwork. Please refer to the DL template link below while the 'Special Requirements' are updated accordingly.

Project Brief:
We need a double sided DL flyer designed for an up market Holiday Rental Company that portrays a personalised approach to property management. These are to be used for letter box drops to homes we're specifically targeting so the design should be modern, complimentary colour palette, uncluttered & visually appealing.

Please Download the DL Template from Quillora here: http://www.quillora.com.au/ql/ns/propath/UploadResources.aspx?selectedTab=0?pfid=KMT&pf_id=KMT&xnav=easypath-upload-image#Templates

Target Market(s)

Wealthy Home Owners

Industry/Entity Type

It Company

Other font styles liked:
• Avant Garde Extra Light & Demi

Colors
33b8a4

Requirements
Must have
• DL Flyer sizes (210mm width x 99mm width, plus 3mm bleed)
• Front: Logo, Main Image & Grab
• Back: Contact Details & Brief Description of our business
• Images: Ideally the main image should be the house with the pool but alternatively a lifestyle images could also be used.
Nice to have
• A creative designer!
Should not have
• Clutter & busy designs

```html
<!DOCTYPE html>
<html lang="en">
<head>
<meta charset="utf-8">
<title>Shoreline Stays – Holiday Rental Management Flyer</title>
<link rel="stylesheet" href="https://fonts.googleapis.com/css2?family=Poppins:wght@200;600&display=swap">
<style>
  :root {
    --brand-teal: #14b196;
    --glow-teal: #7fe3cf;
    --frame-light: #c9f3ea;
    --mark-line: #d6f5ee;
    --text-white: #ffffff;
    --photo-night: #2a2c6e;
    --photo-dusk: #5b4a8f;
    --photo-warm: #c9a36a;
    --photo-pool: #4aa8e6;
  }
  * { margin: 0; padding: 0; box-sizing: border-box; }
  html, body {
    width: 1200px;
    height: 2483px;
    overflow: hidden;
    background: var(--brand-teal);
  }
  .flyer {
    position: relative;
    width: 1200px;
    height: 2483px;
    background: var(--brand-teal);
    color: var(--text-white);
    font-family: "Poppins", "Helvetica Neue", Arial, sans-serif;
  }
  .brand-name {
    position: absolute;
    top: 250px;
    left: 0;
    width: 100%;
    text-align: center;
    font-weight: 200;
    font-size: 140px;
    line-height: 140px;
    letter-spacing: 10px;
    text-transform: uppercase;
  }
  .brand-name span { display: block; }
  .brand-mark {
    position: absolute;
    left: 502px;
    top: 553px;
    width: 196px;
    height: 196px;
    border: 4px solid var(--mark-line);
    border-radius: 50%;
    opacity: 0.85;
  }
  .hero-frame {
    position: absolute;
    left: 50px;
    top: 870px;
    width: 1100px;
    height: 745px;
  }
  .tagline {
    position: absolute;
    font-weight: 600;
    text-transform: uppercase;
    white-space: nowrap;
    line-height: 1;
  }
  .tagline--holiday { left: 158px; top: 1832px; font-size: 68px; }
  .tagline--management { left: 564px; top: 1968px; font-size: 69px; }
  .tagline--difference { left: 326px; top: 2120px; font-size: 54px; }
</style>
</head>
<body>
<main class="flyer">
  <h1 class="brand-name"><span>Shoreline</span><span>Stays</span></h1>
  <div class="brand-mark" aria-hidden="true"></div>

  <svg class="hero-frame" viewBox="0 0 1100 745" xmlns="http://www.w3.org/2000/svg">
    <defs>
      <filter id="frame-glow" x="-10%" y="-10%" width="120%" height="120%">
        <feGaussianBlur stdDeviation="12"/>
      </filter>
      <linearGradient id="photo-tones" x1="0" y1="0" x2="1" y2="1">
        <stop offset="0" stop-color="var(--photo-warm)"/>
        <stop offset="0.35" stop-color="var(--photo-night)"/>
        <stop offset="0.7" stop-color="var(--photo-dusk)"/>
        <stop offset="1" stop-color="var(--photo-pool)"/>
      </linearGradient>
    </defs>
    <path class="frame-glow" d="M60 40 Q550 -10 1040 40 Q1090 372 1040 705 Q550 755 60 705 Q10 372 60 40 Z"
          fill="none" stroke="var(--glow-teal)" stroke-width="26" filter="url(#frame-glow)"/>
    <path class="frame-line" d="M60 40 Q550 -10 1040 40 Q1090 372 1040 705 Q550 755 60 705 Q10 372 60 40 Z"
          fill="none" stroke="var(--frame-light)" stroke-width="5" opacity="0.6"/>
    <path class="hero-photo" role="img" aria-label="Modern luxury holiday home at dusk with a lit swimming pool"
          d="M95 70 Q550 30 1005 70 Q1050 372 1005 675 Q550 715 95 675 Q50 372 95 70 Z"
          fill="url(#photo-tones)"/>
  </svg>

  <p class="tagline tagline--holiday">Holiday Rental</p>
  <p class="tagline tagline--management">Management</p>
  <p class="tagline tagline--difference">With a Difference</p>
</main>
</body>
</html>
```